Awesome Business Card Design needed!

Hey there.
I'm looking for a simple but awesome business card design.
Type of company: Online advertisement agency
(please don't use the typical business people or statistics images on the card)
The front has to display the business name
and possibly some sort of logo ( perhaps something with the two M's of the biz name )
And the back of the card should say:
Name
Phone
Email
Let your imagination flow.
here are some designs that I like and that you can use as inspiration.
Simple but Awesome
http://images.lumavexo.com/designs/55128_877673_43091_thumbnail.jpg
http://images.lumavexo.com/designs/37714_747642_40106_image.jpg
http://images.lumavexo.com/designs/55128_877673_43091_image.jpg
http://images.lumavexo.com/designs/51321_781878_43091_image.jpg
http://images.lumavexo.com/designs/33378_399063_15912_image.jpg
http://images.lumavexo.com/designs/2337_271604_9495_image.jpg
good luck

```html
<!DOCTYPE html>
<html lang="en">
<head>
<meta charset="utf-8">
<title>Verlinde Media — Business Card</title>
<link rel="stylesheet" href="https://fonts.googleapis.com/css2?family=Arimo:wght@400;700&display=swap">
<style>
  :root {
    --page-bg: #2a2a2c;
    --card-base: #101012;
    --card-tile-light: #1e1e21;
    --card-tile-dark: #0b0b0c;
    --brand-blue: #4a9be0;
    --mark-blue: #5fb2ec;
    --text-light: #e4e6ea;
    --text-muted: #b9bcc2;
    --rule: #8a8d93;
  }
  * { box-sizing: border-box; margin: 0; padding: 0; }
  html, body {
    width: 1200px;
    height: 880px;
    overflow: hidden;
    background: var(--page-bg);
    font-family: "Arimo", Arial, sans-serif;
  }
  .canvas {
    width: 1200px;
    height: 880px;
    display: flex;
    align-items: center;
    justify-content: center;
    gap: 40px;
  }
  .card {
    position: relative;
    width: 540px;
    height: 309px;
    background: var(--card-base);
    border-radius: 4px;
    overflow: hidden;
    box-shadow: 0 14px 30px rgba(0, 0, 0, 0.45);
  }
  .card__texture {
    position: absolute;
    inset: 0;
    background: linear-gradient(135deg, var(--card-tile-light) 0%, var(--card-tile-dark) 55%, var(--card-tile-light) 100%);
  }
  .card__content {
    position: relative;
    height: 100%;
    display: flex;
    flex-direction: column;
    align-items: center;
    justify-content: center;
  }
  .brand-mark {
    width: 64px;
    height: 64px;
    background: var(--mark-blue);
    border-radius: 2px;
    margin-bottom: 16px;
  }
  .brand-name {
    font-weight: 700;
    font-size: 34px;
    letter-spacing: 0.5px;
    color: var(--brand-blue);
    text-transform: uppercase;
  }
  .card--back .brand-mark {
    width: 46px;
    height: 46px;
    margin-bottom: 10px;
  }
  .card--back .brand-name {
    font-size: 24px;
    margin-bottom: 22px;
  }
  .contact {
    display: flex;
    flex-direction: column;
    align-items: center;
    text-transform: uppercase;
  }
  .contact__name {
    font-weight: 700;
    font-size: 19px;
    color: var(--text-light);
    letter-spacing: 0.8px;
    padding-bottom: 6px;
    border-bottom: 1px solid var(--rule);
    margin-bottom: 10px;
  }
  .contact__line {
    font-size: 14px;
    color: var(--text-muted);
    letter-spacing: 0.8px;
    line-height: 1.6;
  }
</style>
</head>
<body>
  <main class="canvas">
    <section class="card card--front" aria-label="Card front">
      <div class="card__texture" role="img" aria-label="Subtle dark tiled pattern across the card"></div>
      <div class="card__content">
        <div class="brand-mark"></div>
        <p class="brand-name">Verlinde Media</p>
      </div>
    </section>

    <section class="card card--back" aria-label="Card back">
      <div class="card__texture" role="img" aria-label="Subtle dark tiled pattern across the card"></div>
      <div class="card__content">
        <div class="brand-mark"></div>
        <p class="brand-name">Verlinde Media</p>
        <div class="contact">
          <p class="contact__name">Daniel Brooks</p>
          <p class="contact__line">P: 1221 555 0142</p>
          <p class="contact__line">E: info@verlindemedia.com</p>
        </div>
      </div>
    </section>
  </main>
</body>
</html>
```